IT Company requires new Business Card design.

Over the years we have had a few different business card designs. We are now due for new cards across the board for all staff. We felt this would be a good time to start fresh with a new design. Our traditional card simply had our details on the front, and a list of services on the back. We don't particularly need the list of services, we have had cards where the only thing on the rear of the card was our logo.
Feel free to be creative, we would like our tag line "Complete IT Management" to appear at some point, doesn't necessarily have to be with the logo.
I have attached samples and drafts of various previous cards we have used over the years.

```html
<!DOCTYPE html>
<html lang="en">
<head>
<meta charset="utf-8">
<title>Ridgeview Networks – Business Card</title>
<link rel="stylesheet" href="https://fonts.googleapis.com/css2?family=Open+Sans:wght@400;600;800&display=swap">
<style>
  :root {
    --backdrop: #e4e4ea;
    --metal-dark: #1c1c1e;
    --metal-mid: #3a3a3d;
    --metal-light: #58585c;
    --ink: #ffffff;
    --ink-soft: #d9d9dc;
    --rule: #8a8a8f;
    --mark: #c4c4c8;
  }
  * { box-sizing: border-box; margin: 0; padding: 0; }
  html, body { width: 1200px; height: 987px; overflow: hidden; }
  body {
    background: var(--backdrop);
    font-family: "Open Sans", Arial, sans-serif;
    position: relative;
  }
  .card {
    position: absolute;
    left: 220px;
    width: 760px;
    height: 434px;
    border-radius: 34px;
    overflow: hidden;
    color: var(--ink);
    background:
      linear-gradient(160deg, rgba(255,255,255,0.10) 0%, rgba(255,255,255,0) 45%, rgba(255,255,255,0.06) 70%, rgba(0,0,0,0.25) 100%),
      linear-gradient(100deg, var(--metal-light) 0%, var(--metal-mid) 35%, var(--metal-dark) 100%);
    box-shadow: 0 10px 24px rgba(0,0,0,0.18);
  }
  .card--back { top: 40px; }
  .card--front { top: 513px; }

  .brand { display: flex; align-items: center; gap: 16px; }
  .brand__square { width: 54px; height: 54px; background: var(--mark); }
  .brand__name {
    font-weight: 800;
    text-transform: uppercase;
    line-height: 0.95;
    letter-spacing: 0.5px;
    color: var(--ink);
  }

  /* back */
  .card--back .brand { position: absolute; left: 150px; top: 130px; }
  .card--back .brand__square { width: 92px; height: 92px; }
  .card--back .brand__name { font-size: 50px; }
  .card--back .web {
    position: absolute; left: 0; right: 0; top: 300px;
    text-align: center; font-size: 18px; letter-spacing: 2px; color: var(--ink-soft);
  }

  /* front */
  .card--front .brand { position: absolute; left: 46px; top: 34px; }
  .card--front .brand__name { font-size: 38px; }
  .tagline {
    position: absolute; left: 116px; top: 128px;
    font-size: 12px; letter-spacing: 5px; text-transform: uppercase; color: var(--ink-soft);
  }
  .rule { position: absolute; height: 2px; background: var(--rule); }
  .rule--top { left: 0; right: 0; top: 164px; }
  .rule--bottom { left: 360px; right: 0; top: 318px; }

  .contacts { position: absolute; left: 46px; top: 192px; list-style: none; }
  .contacts li {
    display: flex; align-items: center; gap: 10px;
    font-size: 17px; color: var(--ink-soft); height: 30px;
  }
  .contacts svg { width: 16px; height: 16px; fill: var(--ink-soft); flex: none; }
  .contacts .gap { margin-left: 18px; display: inline-flex; align-items: center; gap: 8px; }

  .person { position: absolute; right: 46px; top: 240px; text-align: right; }
  .person__name { font-size: 24px; font-weight: 800; }
  .person__role { font-size: 18px; color: var(--ink-soft); }
  .address {
    position: absolute; right: 46px; top: 334px; text-align: right;
    font-size: 18px; line-height: 1.4; color: var(--ink-soft);
  }
</style>
</head>
<body>

<section class="card card--back" aria-label="Card back">
  <div class="brand">
    <span class="brand__square"></span>
    <span class="brand__name">Ridgeview<br>Networks</span>
  </div>
  <p class="web">www.ridgeviewnetworks.com.au</p>
</section>

<section class="card card--front" aria-label="Card front">
  <div class="brand">
    <span class="brand__square"></span>
    <span class="brand__name">Ridgeview<br>Networks</span>
  </div>
  <p class="tagline">Complete IT Management</p>
  <div class="rule rule--top"></div>

  <ul class="contacts">
    <li>
      <svg viewBox="0 0 16 16"><path d="M3 1h3l1.5 4-2 1.3a9 9 0 0 0 4.2 4.2L11 8.5l4 1.5v3a2 2 0 0 1-2 2A12 12 0 0 1 1 3a2 2 0 0 1 2-2z"/></svg>
      08 5550 1420
      <span class="gap">
        <svg viewBox="0 0 16 16"><path d="M4 0h8a1 1 0 0 1 1 1v14a1 1 0 0 1-1 1H4a1 1 0 0 1-1-1V1a1 1 0 0 1 1-1zm1 2v9h6V2z"/></svg>
        0400 555 218
      </span>
    </li>
    <li>
      <svg viewBox="0 0 16 16"><path d="M4 1h7v4H4zM1 6h14v7h-3v2H4v-2H1zm4 5v3h6v-3z"/></svg>
      08 5550 1420
    </li>
    <li>
      <svg viewBox="0 0 16 16"><path d="M1 3h14v10H1zm1.5 1.5L8 9l5.5-4.5z"/></svg>
      daniel@ridgeviewnetworks.com.au
    </li>
    <li>
      <svg viewBox="0 0 16 16"><path d="M8 1a7 7 0 1 0 0 14A7 7 0 0 0 8 1zm0 1.5c.9 0 1.9 1.9 2.2 4.7H5.8C6.1 4.4 7.1 2.5 8 2.5zM2.6 8.8h2.1c.1 1.6.4 3 .9 4A5.5 5.5 0 0 1 2.6 8.8zm0-1.6a5.5 5.5 0 0 1 3-4c-.5 1-.8 2.4-.9 4zm5.4 6.3c-.9 0-1.9-1.9-2.2-4.7h4.4c-.3 2.8-1.3 4.7-2.2 4.7zm2.4-.7c.5-1 .8-2.4.9-4h2.1a5.5 5.5 0 0 1-3 4zm.9-5.6c-.1-1.6-.4-3-.9-4a5.5 5.5 0 0 1 3 4z"/></svg>
      www.ridgeviewnetworks.com.au
    </li>
  </ul>

  <div class="person">
    <p class="person__name">Daniel Hart</p>
    <p class="person__role">Operation Manager</p>
  </div>
  <div class="rule rule--bottom"></div>
  <p class="address">Unit 4 12 Harlow Street<br>Ashbury Vale WA 6150</p>
</section>

</body>
</html>
```